Computer Company needs a Business card design

We need a business card design for our business. We assist people to transition to the KVS (Kestrel Vantage Scheme). The Verandal Crown Office-owned kvs™ network is a brand new telecommunications network currently being rolled out across Australia, giving access to a reliable broadband connection. Our niche market will predominantly be domestic customers in the 50+ age bracket. The assistance that we provide is everything from arranging the equipment, arranging the plan and contract term, appointment times, final testing of the network and any tweaks that need to be made. We basically PM the transition from start to finish. The business card design should be minimalist, should communicate loyalty and stability, should be easy to read and clearly explain what we do. We have asked for front and back. However, the back of the card does not have to include much information at all. It could be just a small design, or a repeat of our phone number. Up to you. The attached file only says what is required on the card. It does not specify where to arrange the text, what fonts to use, etc etc. As much as we would like to give you more info, due to our very limited design ability, we are not really able to send you any rough, or otherwise, designs of what we are after. Hopefully the above description is enough for you.

```html
<!DOCTYPE html>
<html lang="en">
<head>
<meta charset="utf-8">
<title>Homeline Assist — Business Card</title>
<link rel="stylesheet" href="https://fonts.googleapis.com/css2?family=Jost:wght@500;600&family=Questrial&display=swap">
<style>
  :root {
    --brand-blue: #0784ad;
    --backdrop: #d6d6d6;
    --card-white: #f7f7f7;
    --text-grey: #9a9a9a;
    --text-dark: #555555;
    --white: #ffffff;
  }
  * { margin: 0; padding: 0; box-sizing: border-box; }
  html, body {
    width: 1200px;
    height: 960px;
    overflow: hidden;
    background: var(--backdrop);
  }
  .canvas {
    position: relative;
    width: 1200px;
    height: 960px;
  }
  .card {
    position: absolute;
    left: 320px;
    width: 600px;
    height: 342px;
  }
  .card-front {
    top: 100px;
    background: var(--brand-blue);
    display: flex;
    align-items: center;
    justify-content: center;
  }
  .card-back {
    top: 493px;
    background: var(--card-white);
  }
  .wordmark {
    font-family: "Jost", sans-serif;
    font-weight: 500;
    line-height: 1;
    white-space: nowrap;
  }
  .card-front .wordmark {
    color: var(--white);
    font-size: 56px;
  }
  .card-back .wordmark {
    position: absolute;
    left: 67px;
    top: 100px;
    font-size: 61px;
    color: var(--brand-blue);
  }
  .holder {
    position: absolute;
    left: 67px;
    top: 208px;
  }
  .holder-name {
    font-family: "Jost", sans-serif;
    font-weight: 600;
    font-size: 20px;
    letter-spacing: 0.8px;
    color: var(--brand-blue);
    line-height: 24px;
  }
  .holder-role {
    font-family: "Questrial", sans-serif;
    font-size: 15px;
    letter-spacing: 0.4px;
    color: var(--text-grey);
    line-height: 20px;
  }
  .contact-list {
    position: absolute;
    right: 84px;
    top: 208px;
    list-style: none;
    font-family: "Questrial", sans-serif;
    font-size: 15px;
    letter-spacing: 0.2px;
    color: var(--text-dark);
    text-align: right;
  }
  .contact-list li {
    display: flex;
    align-items: center;
    justify-content: flex-end;
    gap: 7px;
    height: 20px;
  }
  .contact-icon {
    width: 13px;
    height: 13px;
    fill: var(--brand-blue);
  }
</style>
</head>
<body>
<main class="canvas">
  <section class="card card-front" aria-label="Card front">
    <p class="wordmark">Homeline Assist</p>
  </section>

  <section class="card card-back" aria-label="Card back">
    <p class="wordmark">Homeline Assist</p>

    <div class="holder">
      <p class="holder-name">OWEN TALLIS</p>
      <p class="holder-role">CEO/FOUNDER</p>
    </div>

    <ul class="contact-list">
      <li>0412587309
        <svg class="contact-icon" viewBox="0 0 16 16" aria-hidden="true">
          <path d="M3.6 1.2l2.3 2.9c.3.4.3.9 0 1.3L4.8 6.6c.9 2 2.6 3.7 4.6 4.6l1.2-1.1c.4-.3.9-.3 1.3 0l2.9 2.3c.4.3.4.9.1 1.3l-1.2 1.4c-.5.5-1.2.7-1.9.5C6.8 14.2 1.8 9.2.4 4.2.2 3.5.4 2.8.9 2.3L2.3 1.1c.4-.3 1-.3 1.3.1z"/>
        </svg>
      </li>
      <li>owen@homelineassist.com.au
        <svg class="contact-icon" viewBox="0 0 16 16" aria-hidden="true">
          <path d="M1 3h14v10H1z M1 3l7 5.5L15 3" fill="var(--brand-blue)" stroke="var(--card-white)" stroke-width="1"/>
        </svg>
      </li>
      <li>www.homelineassist.com.au
        <svg class="contact-icon" viewBox="0 0 16 16" aria-hidden="true">
          <circle cx="8" cy="8" r="7"/>
          <path d="M1 8h14M8 1c2.5 2.5 2.5 11.5 0 14M8 1c-2.5 2.5-2.5 11.5 0 14" fill="none" stroke="var(--card-white)" stroke-width="1"/>
        </svg>
      </li>
    </ul>
  </section>
</main>
</body>
</html>
```